New Alcoholic Spiked Seltzer Line

We need a can design for a line of low calorie alcoholic seltzer. This product is a sparkling water and vodka drink with no sugar added in a slim 12 oz can.

This is a lighter, healthier, alternative to the sugary ready-to-drinks on the market. The product contains only 3 ingredients: Vodka, Water and Natural Flavors. It has only 100 calories but still has 5% alcohol, so you don't need to sacrifice alcohol to cut calories.

This product also does not contain any preservatives.

We want this design to communicate the following objectives to the consumer and in this order:

1. Appetizing product
2.Low calorie
3.Communicate the type of beverage (Spiked Seltzer)

The brand name of the product is VELKA.

The flavor of the product needed to be used for the design is Mango-Orange.

Comparable products are:

www.brindlefizzworks.example/
https://www.quorvabubbles.example
https://pelnavo.example/

The designs should not infringe or copy the creative directions of the products mentionned above. They are only given so that you can better understand the type of product we are developing.

Target Market(s)

Young Professional women between the ages of 25 and 44

Industry/Entity Type

Product

Colors

Designer to choose colors to be used in the design.

Requirements
Must have
• Design extendibility, meaning it can be adapted for other flavors.
• This is a new category in the market we are targeting, so consumers must easily be able to identify what type of product this is.

```html
<!DOCTYPE html>
<html lang="en">
<head>
<meta charset="utf-8">
<title>VELKA Spiked Seltzer – Can Labels</title>
<link rel="stylesheet" href="https://fonts.googleapis.com/css2?family=Playfair+Display:ital,wght@0,400;0,500;1,400&family=Josefin+Sans:wght@400;600&family=Quicksand:wght@500;600&display=swap">
<style>
  :root {
    --backdrop: #e9e9ea;
    --ink-light: #ffffff;
    --lemon-a: #9ccc2e;
    --lemon-b: #27b9a8;
    --lemon-ink: #6aa51f;
    --cran-a: #7a2aa0;
    --cran-b: #d8289a;
    --cran-ink: #7a2aa0;
    --passion-a: #e8242f;
    --passion-b: #f2892a;
    --passion-ink: #e0262f;
    --mango-a: #f6b51e;
    --mango-b: #f08a1c;
    --mango-ink: #f2a12a;
  }
  * { margin: 0; padding: 0; box-sizing: border-box; }
  html, body {
    width: 1200px;
    height: 794px;
    overflow: hidden;
    background: var(--backdrop);
  }
  .flavour-range {
    width: 1200px;
    height: 794px;
    display: flex;
    justify-content: center;
    align-items: center;
    gap: 30px;
  }
  .can-label {
    width: 250px;
    height: 600px;
    display: block;
    border-radius: 4px;
    overflow: hidden;
    box-shadow: 0 2px 10px rgba(0,0,0,0.08);
  }
  .can-label svg { display: block; width: 250px; height: 600px; }
  .tagline {
    font-family: "Josefin Sans", sans-serif;
    font-size: 13px;
    letter-spacing: 3px;
    fill: var(--ink-light);
  }
  .arc-claim {
    font-family: "Josefin Sans", sans-serif;
    font-size: 12px;
    letter-spacing: 2.4px;
    fill: var(--ink-light);
  }
  .brand-name {
    font-family: "Playfair Display", serif;
    font-size: 66px;
    font-weight: 400;
    fill: var(--ink-light);
  }
  .category {
    font-family: "Playfair Display", serif;
    font-style: italic;
    font-size: 52px;
    fill: var(--ink-light);
  }
  .facts {
    font-family: "Quicksand", sans-serif;
    font-weight: 600;
    font-size: 16px;
    fill: var(--ink-light);
  }
  .flavour-pill { fill: #ffffff; }
  .flavour-name {
    font-family: "Quicksand", sans-serif;
    font-weight: 600;
    font-size: 15px;
    letter-spacing: 0.5px;
  }
  .lemon .flavour-name { fill: var(--lemon-ink); }
  .cranberry .flavour-name { fill: var(--cran-ink); }
  .passion .flavour-name { fill: var(--passion-ink); }
  .mango .flavour-name { fill: var(--mango-ink); }
</style>
</head>
<body>
<main class="flavour-range">

  <!-- Lemon Twist -->
  <article class="can-label lemon">
    <svg viewBox="0 0 250 600" xmlns="http://www.w3.org/2000/svg">
      <defs>
        <linearGradient id="lemon-wash" x1="0" y1="0" x2="0.4" y2="1">
          <stop offset="0" stop-color="#8fd23a"/>
          <stop offset="0.5" stop-color="#3fbf8a"/>
          <stop offset="1" stop-color="#22b6b0"/>
        </linearGradient>
        <path id="lemon-top" d="M5 300 A120 120 0 0 1 245 300"/>
        <path id="lemon-bottom" d="M5 300 A120 120 0 0 0 245 300"/>
      </defs>
      <rect class="label-artwork" width="250" height="600" fill="url(#lemon-wash)" role="img" aria-label="Flowing ribbon line pattern in lime green and teal"/>
      <rect class="rim-band" width="250" height="24" fill="var(--lemon-a)"/>
      <rect class="rim-band" y="576" width="250" height="24" fill="var(--lemon-a)"/>
      <text class="tagline"><textPath href="#lemon-top" startOffset="50%" text-anchor="middle">THE NEW COOL</textPath></text>
      <text class="brand-name" x="125" y="262" text-anchor="middle" textLength="228" lengthAdjust="spacingAndGlyphs">VELKA</text>
      <text class="category" x="118" y="322" text-anchor="middle">Spiked</text>
      <text class="category" x="132" y="376" text-anchor="middle">Seltzer</text>
      <text class="arc-claim"><textPath href="#lemon-bottom" startOffset="50%" text-anchor="middle">ENRICHED WITH NATURAL FLAVOURS</textPath></text>
      <text class="facts" x="125" y="468" text-anchor="middle">ONLY 100 CALORIES</text>
      <text class="facts" x="125" y="489" text-anchor="middle">5% ALC/VOL</text>
      <rect class="flavour-pill" x="60" y="506" width="130" height="32" rx="14"/>
      <text class="flavour-name" x="125" y="528" text-anchor="middle">LEMON TWIST</text>
    </svg>
  </article>

  <!-- Cranberry Crush -->
  <article class="can-label cranberry">
    <svg viewBox="0 0 250 600" xmlns="http://www.w3.org/2000/svg">
      <defs>
        <linearGradient id="cran-wash" x1="0" y1="0" x2="0.5" y2="1">
          <stop offset="0" stop-color="#b02fb0"/>
          <stop offset="0.5" stop-color="#d8289a"/>
          <stop offset="1" stop-color="#6f2aa6"/>
        </linearGradient>
        <path id="cran-top" d="M5 300 A120 120 0 0 1 245 300"/>
        <path id="cran-bottom" d="M5 300 A120 120 0 0 0 245 300"/>
      </defs>
      <rect class="label-artwork" width="250" height="600" fill="url(#cran-wash)" role="img" aria-label="Flowing ribbon line pattern in magenta and purple"/>
      <rect class="rim-band" width="250" height="24" fill="var(--cran-a)"/>
      <rect class="rim-band" y="576" width="250" height="24" fill="var(--cran-a)"/>
      <text class="tagline"><textPath href="#cran-top" startOffset="50%" text-anchor="middle">THE NEW COOL</textPath></text>
      <text class="brand-name" x="125" y="262" text-anchor="middle" textLength="228" lengthAdjust="spacingAndGlyphs">VELKA</text>
      <text class="category" x="118" y="322" text-anchor="middle">Spiked</text>
      <text class="category" x="132" y="376" text-anchor="middle">Seltzer</text>
      <text class="arc-claim"><textPath href="#cran-bottom" startOffset="50%" text-anchor="middle">ENRICHED WITH NATURAL FLAVOURS</textPath></text>
      <text class="facts" x="125" y="468" text-anchor="middle">ONLY 100 CALORIES</text>
      <text class="facts" x="125" y="489" text-anchor="middle">5% ALC/VOL</text>
      <rect class="flavour-pill" x="48" y="506" width="154" height="32" rx="14"/>
      <text class="flavour-name" x="125" y="528" text-anchor="middle">CRANBERRY CRUSH</text>
    </svg>
  </article>

  <!-- Passion Fruity -->
  <article class="can-label passion">
    <svg viewBox="0 0 250 600" xmlns="http://www.w3.org/2000/svg">
      <defs>
        <linearGradient id="passion-wash" x1="0" y1="0" x2="0.5" y2="1">
          <stop offset="0" stop-color="#ee3a2a"/>
          <stop offset="0.5" stop-color="#f2702c"/>
          <stop offset="1" stop-color="#e8242f"/>
        </linearGradient>
        <path id="passion-top" d="M5 300 A120 120 0 0 1 245 300"/>
        <path id="passion-bottom" d="M5 300 A120 120 0 0 0 245 300"/>
      </defs>
      <rect class="label-artwork" width="250" height="600" fill="url(#passion-wash)" role="img" aria-label="Flowing ribbon line pattern in red and orange"/>
      <rect class="rim-band" width="250" height="24" fill="var(--passion-a)"/>
      <rect class="rim-band" y="576" width="250" height="24" fill="var(--passion-a)"/>
      <text class="tagline"><textPath href="#passion-top" startOffset="50%" text-anchor="middle">THE NEW COOL</textPath></text>
      <text class="brand-name" x="125" y="262" text-anchor="middle" textLength="228" lengthAdjust="spacingAndGlyphs">VELKA</text>
      <text class="category" x="118" y="322" text-anchor="middle">Spiked</text>
      <text class="category" x="132" y="376" text-anchor="middle">Seltzer</text>
      <text class="arc-claim"><textPath href="#passion-bottom" startOffset="50%" text-anchor="middle">ENRICHED WITH NATURAL FLAVOURS</textPath></text>
      <text class="facts" x="125" y="468" text-anchor="middle">ONLY 100 CALORIES</text>
      <text class="facts" x="125" y="489" text-anchor="middle">5% ALC/VOL</text>
      <rect class="flavour-pill" x="52" y="506" width="146" height="32" rx="14"/>
      <text class="flavour-name" x="125" y="528" text-anchor="middle">PASSION FRUITY</text>
    </svg>
  </article>

  <!-- Mango-Orange -->
  <article class="can-label mango">
    <svg viewBox="0 0 250 600" xmlns="http://www.w3.org/2000/svg">
      <defs>
        <linearGradient id="mango-wash" x1="0" y1="0" x2="0.5" y2="1">
          <stop offset="0" stop-color="#f7b52a"/>
          <stop offset="0.5" stop-color="#f28a22"/>
          <stop offset="1" stop-color="#f6a020"/>
        </linearGradient>
        <path id="mango-top" d="M5 300 A120 120 0 0 1 245 300"/>
        <path id="mango-bottom" d="M5 300 A120 120 0 0 0 245 300"/>
      </defs>
      <rect class="label-artwork" width="250" height="600" fill="url(#mango-wash)" role="img" aria-label="Flowing ribbon line pattern in mango yellow and orange"/>
      <rect class="rim-band" width="250" height="24" fill="var(--mango-a)"/>
      <rect class="rim-band" y="576" width="250" height="24" fill="var(--mango-a)"/>
      <text class="tagline"><textPath href="#mango-top" startOffset="50%" text-anchor="middle">THE NEW COOL</textPath></text>
      <text class="brand-name" x="125" y="262" text-anchor="middle" textLength="228" lengthAdjust="spacingAndGlyphs">VELKA</text>
      <text class="category" x="118" y="322" text-anchor="middle">Spiked</text>
      <text class="category" x="132" y="376" text-anchor="middle">Seltzer</text>
      <text class="arc-claim"><textPath href="#mango-bottom" startOffset="50%" text-anchor="middle">ENRICHED WITH NATURAL FLAVOURS</textPath></text>
      <text class="facts" x="125" y="468" text-anchor="middle">ONLY 100 CALORIES</text>
      <text class="facts" x="125" y="489" text-anchor="middle">5% ALC/VOL</text>
      <rect class="flavour-pill" x="54" y="506" width="142" height="32" rx="14"/>
      <text class="flavour-name" x="125" y="528" text-anchor="middle">MANGO-ORANGE</text>
    </svg>
  </article>

</main>
</body>
</html>
```